Revamp Kestrelo Inc website

A complete revamp of the www.kestrelo-app.com website.
Strong actionable landing pages.
An in-house site was being done but was abandoned. See http://www.sitebuildly.com/dmorvane/kestrelo and once in, click on the "Home" to go to the main Home page.
Updates

A new YouTube Standard Video has just been posted: http://www.clipvista.com/watch?v=Q-T8ma4zLpW&feature=email

I thought that I would share what was being done in-house, but was abandoned.

Once launched you will come to the main landing page, then click on the "Home" button to see the main home page. I thought this was rather interesting. One problem here is Flash, most smartphones don't support Flash and our market is in that world, so Flash really is not a good option.

Reason: Please can you submit one more design, we have a dead tie with voting.

Reason: Request as per a designer.

Target Market(s)

Kestrelo for all intense purposes is mobile RoadHalo on steroids. Currently running on Droidix, BB and uPhone. End of Jan 2012 we will run on ANY J2ME (Java) supported phone as well. Here we will be talking directly to the OBD (onboard diagnostics) in the car. In the event of the car's airbags being deployed emergency services, ES, (whether public, 911 or other country equivalent, or private, alarm company) the application will not only call the ES but also log the gps information. Other services include: SOS, Nurse Lines, Roadside, Notify Friends and Family.
Kestrelo determines the ERC by the phones location, thus assuming not private in the USA will reach out to 911, Europe 112 etc.

Kestrelo is about making a pro and re active emergency solution to the masses. It must be affordable to anyone owning a cell phone (thus: 9 cents per day). The emphasis is on the person not the asset as RoadHalo and other competitors are. It must be adaptable to ones environment

Kestrelo target market sale is a top-down (Corporate to consumer) we do offer:
* white-labeling (see www.guardlinemobileus.com) as well as non branded solutions (Kestrelo branded),
* private emergency response center call and data routing - here the emergency call is routed the the companies emergency call center (example: alarm company, security firm, campus police), and the location and user details data details on file are pushed as well.

As such our target corporate market primarily is:
Security, Home Alarm, Insurance, University Campus Police, Auto, Smartphone users, Roadside assistance

Our ultimate target audience is cell phone users, where security, safety and peace of mind of oneself, family and/or team members is of importance.

Requirements
Must have
• Must have strong actionable call to action features
Must have multiple actionable landing pages
Must link to our ecommerce
Must link into blog
Must be able to cellphone friendly (i.e.: no flash)
Must be SEO

```html
<!DOCTYPE html>
<html lang="en">
<head>
<meta charset="utf-8">
<title>Kestrelo, Inc. | Accident Response &amp; Mobile GPS Tracking</title>
<link rel="stylesheet" href="https://fonts.googleapis.com/css2?family=Michroma&family=Open+Sans:wght@400;600;700&display=swap">
<style>
:root{
  --ink:#333;
  --ink-soft:#555;
  --navy:#1d3a57;
  --blue:#3b6a94;
  --blue-dark:#264d72;
  --blue-light:#5d8bb5;
  --red:#b0121b;
  --page:#e9e9e9;
  --panel:#f7f7f7;
  --white:#fff;
  --logo:#e3e3e3;
}
*{box-sizing:border-box;margin:0;padding:0}
html,body{width:841px;height:1200px;overflow:hidden}
body{position:relative;background:var(--page);font-family:Arial,"Helvetica Neue",sans-serif;color:var(--ink)}
.abs{position:absolute}

/* header */
.site-header{left:0;top:0;width:841px;height:132px;background:linear-gradient(#ffffff,#ececec);border-bottom:2px solid #d8d8d8}
.brand{left:74px;top:18px;font-family:"Michroma",sans-serif;font-size:50px;color:var(--logo);letter-spacing:-1px;line-height:1}
.phone{left:613px;top:14px;display:flex;align-items:center;gap:10px;font-family:"Open Sans",sans-serif;font-size:19px;color:var(--navy)}
.phone-icon{width:26px;height:26px;background:var(--blue);border-radius:4px;display:flex;align-items:center;justify-content:center}
.search{left:614px;top:55px;width:146px;height:28px;background:var(--white);border:1px solid #cfcfcf;border-radius:4px;box-shadow:inset 0 1px 3px rgba(0,0,0,.15)}
.search-btn{position:absolute;right:4px;top:3px;width:20px;height:20px;border-radius:50%;background:#2b7fc7}
.main-nav{left:65px;top:97px;width:706px;height:32px;background:linear-gradient(#f7f7f7,#dcdcdc);border:1px solid #d0d0d0}
.main-nav a{position:absolute;top:8px;font-size:11px;color:#222;text-decoration:none;letter-spacing:.2px}
.main-nav a.current{top:3px;left:31px;width:61px;height:25px;line-height:25px;text-align:center;color:var(--white);background:var(--blue);border-radius:2px}

/* hero */
.hero-frame{left:65px;top:150px;width:708px;height:258px;background:var(--white);border:1px solid #ccc;box-shadow:0 6px 10px rgba(0,0,0,.18)}
.hero-photo{left:9px;top:9px;width:686px;height:237px;background:linear-gradient(100deg,#5c6a7a 0%,#8b95a0 35%,#a7a9aa 60%,#c9ccce 100%)}
.hero-lead{left:16px;top:66px;width:360px;font-family:"Open Sans",sans-serif;font-weight:700;font-size:17.5px;line-height:27px;color:var(--white);text-shadow:1px 1px 2px rgba(0,0,0,.6)}
.hero-price{right:18px;bottom:32px;font-family:"Open Sans",sans-serif;font-weight:700;font-size:16px;color:var(--white);text-shadow:1px 1px 2px rgba(0,0,0,.6)}
.hero-arrow{top:270px;width:28px;height:28px;border-radius:50%;background:var(--white);box-shadow:0 1px 3px rgba(0,0,0,.3);text-align:center;line-height:26px;font-size:18px;font-weight:700;color:#333}

/* intro */
.intro{left:0;top:426px;width:841px;height:307px;background:var(--white)}
.cta{left:80px;width:167px;height:57px;border-radius:4px;background:linear-gradient(var(--blue-light),var(--blue-dark));box-shadow:0 2px 4px rgba(0,0,0,.25);color:var(--white);font-family:"Open Sans",sans-serif}
.cta-get{top:30px}
.cta-get .big{position:absolute;left:40px;top:13px;font-size:15px}
.cta-get .small{position:absolute;left:100px;top:36px;font-size:9px}
.cta-phone{top:105px;font-size:13px;text-align:center;line-height:57px}
.platforms{left:80px;top:181px;width:167px;height:103px;background:var(--white);border-radius:4px;box-shadow:0 1px 5px rgba(0,0,0,.2)}
.platform-dot{position:absolute;top:14px;width:30px;height:30px;border-radius:50%}
.platform-name{position:absolute;left:0;width:167px;top:70px;text-align:center;font-size:15px;font-weight:700;color:#222}
.intro-title{left:286px;top:27px;font-size:13px;font-weight:700;line-height:22px;color:var(--navy)}
.intro-body{left:286px;top:86px;width:490px;font-size:9.8px;line-height:18px;color:var(--ink)}
.feature-list{list-style:none;font-size:9.8px;line-height:18px}
.feature-list li{position:relative;padding-left:16px}
.feature-list li::before{content:"\00BB";position:absolute;left:0;font-weight:700;font-size:12px}
.features-a{left:292px;top:154px;width:290px}
.features-b{left:594px;top:154px;width:225px}

/* media */
.video{left:57px;top:753px;width:355px;height:216px;background:#000;border:1px solid #999}
.video-slide{left:2px;top:2px;width:349px;height:194px;background:linear-gradient(160deg,#1e4e5a 0%,#0f2f3a 45%,#07161d 100%);color:var(--white);font-family:"Open Sans",sans-serif}
.video-slide h3{position:absolute;left:58px;top:14px;font-size:14px;font-weight:400}
.video-slide ul{position:absolute;left:60px;top:44px;list-style:none;font-size:12px;line-height:16.5px}
.video-slide .sub{padding-left:14px}
.video-bar{left:2px;top:198px;width:349px;height:14px;background:linear-gradient(#3a3a3a,#111);font-size:6px;color:#ddd}
.video-progress{left:0;top:0;width:349px;height:2px;background:#555}
.video-progress::before{content:"";position:absolute;left:0;top:0;width:72%;height:2px;background:#c00}
.testimonials-title{left:444px;top:749px;font-size:13px;font-weight:700;color:var(--navy)}
.bubble{left:443px;width:338px;background:var(--white);border-radius:6px;box-shadow:0 1px 4px rgba(0,0,0,.15);padding:8px 12px;font-size:7.8px;line-height:11.5px;color:#333}
.bubble cite{display:block;font-style:normal;color:var(--red)}
.bubble-1{top:767px;height:88px}
.bubble-2{top:859px;height:100px}
.bubble p+p{margin-top:8px}

/* footer */
.footer{left:0;top:976px;width:841px;height:138px;background:linear-gradient(#e4e4e4,#f2f2f2);border-top:2px solid #d0d0d0}
.connect{left:52px;top:13px;width:163px;height:120px;background:var(--panel);border-radius:4px}
.connect h4{position:absolute;left:18px;top:14px;font-size:11px;font-weight:400;color:#222}
.social{position:absolute;top:49px;width:16px;height:16px;border-radius:2px}
.link-panel{left:224px;top:13px;width:560px;height:120px;background:var(--panel);border-radius:4px}
.link-col{position:absolute;top:18px}
.link-col h4{font-size:9px;font-weight:700;color:var(--navy);margin-bottom:10px}
.link-col ul{list-style:none;font-size:8px;line-height:18px;padding-left:6px}
.link-col li::before{content:">>  ";white-space:pre}
.base{left:0;top:1114px;width:841px;height:86px;background:linear-gradient(#f4f4f4,#e2e2e2)}
.base-brand{left:68px;top:22px;font-family:"Michroma",sans-serif;font-size:31px;color:var(--white);letter-spacing:-1px}
.base-links{left:410px;top:25px;width:316px;text-align:center;font-size:9px;color:#222}
.base-links span{margin:0 10px}
.copyright{left:410px;top:47px;width:316px;text-align:center;font-size:8.5px;color:#222}
</style>
</head>
<body>

<header class="site-header abs">
  <div class="brand abs">Kestrelo, Inc.</div>
  <div class="phone abs">
    <span class="phone-icon">
      <svg width="14" height="16" viewBox="0 0 14 16"><path d="M3 1h3l1 4-2 1.5c.8 2 2.3 3.6 4 4.5L10.5 9l3.5 1v3c0 1-1 2-2 2C6 15 1 9 1 3c0-1 1-2 2-2z" fill="#fff"/></svg>
    </span>
    555.014.2287
  </div>
  <div class="search abs">
    <span class="search-btn">
      <svg width="20" height="20" viewBox="0 0 20 20"><circle cx="9" cy="9" r="4" fill="none" stroke="#fff" stroke-width="1.8"/><path d="M12 12l3 3" stroke="#fff" stroke-width="2"/></svg>
    </span>
  </div>
  <nav class="main-nav abs">
    <a class="current" href="#">HOME</a>
    <a style="left:110px" href="#">ABOUT US</a>
    <a style="left:192px" href="#">SERVICES</a>
    <a style="left:274px" href="#">PARTNERS</a>
    <a style="left:359px" href="#">CONTACT US</a>
    <a style="left:454px" href="#">PURCHASE</a>
    <a style="left:543px" href="#">LOGIN</a>
  </nav>
</header>

<section class="hero-frame abs">
  <div class="hero-photo abs" role="img" aria-label="Photo of a woman calling for help on her mobile phone beside a damaged car on a highway">
    <p class="hero-lead abs">Introducing Kestrelo, the ultimate mobile solution for automatic emergency alerts and response . . .</p>
    <p class="hero-price abs">All For 9 Cents Per Day</p>
  </div>
</section>
<div class="hero-arrow abs" style="left:50px">&laquo;</div>
<div class="hero-arrow abs" style="left:756px">&raquo;</div>

<section class="intro abs">
  <a class="cta cta-get abs" href="#"><span class="big">Get it Now!</span><span class="small">Kestrelo</span></a>
  <a class="cta cta-phone abs" href="#">uPhone User Clickhere</a>
  <div class="platforms abs">
    <span class="platform-dot" style="left:40px;background:#8cc63f"></span>
    <span class="platform-dot" style="left:98px;background:#e0663a"></span>
    <span class="platform-name">BerryLine</span>
  </div>

  <h1 class="intro-title abs">Kestrelo | Accident Response, Personal GPS Tracker,<br>Mobile GPS Tracking, Roadside</h1>
  <p class="intro-body abs">No matter the emergency, Kestrelo instantaneously triggers an emergency response call conveying your exact location and other critical information to emergency personnel.&nbsp; Kestrelo’s comprehensive service also provides the following features:</p>
  <ul class="feature-list features-a abs">
    <li>Accident and Impact Management (patent pending)</li>
    <li>High Crime Area Alerts</li>
    <li>International and National SOS</li>
    <li>Cyber Alert Notification Management</li>
    <li>Personal Location Notification</li>
    <li>Homeland and Travel Status Notification</li>
    <li>24/7 Certified Nurse Line</li>
  </ul>
  <ul class="feature-list features-b abs">
    <li>Traffic Alerts</li>
    <li>Auto Assistance</li>
    <li>Extensive Online Tracking Management Portal</li>
    <li>Weather Alert</li>
    <li>Including: Geo-Fencing, Trip Reporting, Speed Reporting, Incident Tracking and Reporting</li>
  </ul>
</section>

<div class="video abs">
  <div class="video-slide abs" role="img" aria-label="Video presentation slide on a dark teal background">
    <h3>Features: GPS Location, Geo-fencing</h3>
    <ul>
      <li>○ Complete, full-featured, location-based</li>
      <li>&nbsp;&nbsp;&nbsp;services solutions available online, i.e.</li>
      <li class="sub">• Geo-fencing &amp; boundary crossings</li>
      <li class="sub">• Client profiling</li>
      <li class="sub">• Tracking &amp; Trailing</li>
      <li class="sub">• Speeding</li>
      <li class="sub">• Extensive Reporting</li>
      <li>○ Architecture supports fleet management</li>
    </ul>
  </div>
  <div class="video-bar abs">
    <div class="video-progress abs"></div>
    <svg class="abs" style="left:8px;top:4px" width="40" height="8" viewBox="0 0 40 8"><rect x="0" y="0" width="2" height="7" fill="#ddd"/><rect x="4" y="0" width="2" height="7" fill="#ddd"/><path d="M30 2h3l3-2v8l-3-2h-3z" fill="#ddd"/></svg>
    <span class="abs" style="left:55px;top:4px">2:31 / 3:28</span>
    <span class="abs" style="left:285px;top:4px">360p</span>
  </div>
</div>

<h2 class="testimonials-title abs">Testimonials</h2>
<blockquote class="bubble bubble-1 abs">
  <p>"I drive 40 minutes to work at 2 in the morning. If I were to get in an accident, work would assume I was sick, and my wife would be home sleeping peacefully. I feel much safer knowing that I have someone watching over me and making sure I travel safely with the Kestrelo smart-phone app. Great job, Kestrelo!"</p>
  <cite>&nbsp;&nbsp;- Dana Whitlock</cite>
</blockquote>
<blockquote class="bubble bubble-2 abs">
  <p>"...Knocked out, my car completely trashed, I woke up to find the police and ambulance had already been informed by Kestrelo. Thanks Kestrelo for doing what you said you would"<cite>- Glen</cite></p>
  <p>"....what was the life saviour, was the fact kestrelo sent along to coordinates of where I was...I think your product is great... Thanks once again"<cite>- Marco Veillette</cite></p>
</blockquote>

<footer class="footer abs">
  <div class="connect abs">
    <h4>Connect Us &nbsp;:</h4>
    <span class="social" style="left:18px;background:#3b5998"></span>
    <span class="social" style="left:48px;background:#4fb7e6"></span>
    <span class="social" style="left:78px;background:#f57d00"></span>
    <span class="social" style="left:108px;background:#0e76a8"></span>
    <span class="social" style="left:138px;background:#6aa84f"></span>
  </div>
  <div class="link-panel abs">
    <div class="link-col" style="left:15px"><h4>Application&nbsp; Download</h4><ul><li>BerryLine</li><li>uPhone</li><li>Droidix</li></ul></div>
    <div class="link-col" style="left:159px"><h4>Kestrelo Services and Policies</h4><ul><li>Privacy Policy</li><li>Terms &amp; Conditions</li></ul></div>
    <div class="link-col" style="left:317px"><h4>Company/Marketing</h4><ul><li>Affiliate Program</li></ul></div>
    <div class="link-col" style="left:446px"><h4>Kestrelo News and Events</h4><ul><li>News and Events</li><li>Live Chat</li></ul></div>
  </div>
</footer>

<div class="base abs">
  <div class="base-brand abs">Kestrelo, Inc.</div>
  <div class="base-links abs">Privacy Policy<span>|</span>Terms &amp; Conditions<span>|</span>Contact Us</div>
  <div class="copyright abs">Copyright © KESTRELO, Inc. All Rights Reserved</div>
</div>

</body>
</html>
```